Four in One (Flexible infographic for Content Management Industry)

See attachment.
A graphic depicting 4 products, where each can stand on its own and each can be combined with others, but where, if all are taken together, the best result is achieved (the "super product").
Intended use is web. See attached file as an example.
The most basic idea is as the attached diagram shows, where 4 rectangles are arranged in a quadrangle, with a middle rectangle in the center representing the combined 4 products. This concept is fine except it is a bit too obvious as it stands. We are looking for either a variation of this or another concept.
The audience is technical + professional + enterprise - NOT consumers. Hence the design should be conservative in nature.
We are aware of tools like as Canva or Pictogram where such graphics are available, but we are looking for something with a bit more imagination and flexibility.
This graphic should be targeted to web sites and be delivered with vector-based (SVG) graphics.

```html
<!DOCTYPE html>
<html lang="en">
<head>
<meta charset="utf-8">
<title>Super Product – Four in One Infographic</title>
<link rel="stylesheet" href="https://fonts.googleapis.com/css2?family=Rubik:wght@500;700&family=Roboto:wght@400;500&display=swap">
<style>
  :root {
    --white: #ffffff;
    --ink: #222326;
    --frame: #4a4a4a;
    --ring: #e4e5e7;
    --blue-doc: #3a5a99;
    --blue-sec: #4f6491;
    --blue-erp-a: #3a6aa3;
    --blue-erp-b: #4584b1;
    --blue-dig: #7c9cc1;
    --line-doc: #3b3a8f;
    --line-sec: #6b2f5f;
    --line-erp: #c48a1a;
    --line-dig: #4ea8b0;
    --icon-doc: #3b3a8f;
    --icon-sec: #a3277b;
    --icon-erp: #e8873a;
    --icon-dig: #3fb3b8;
  }
  html, body { margin: 0; padding: 0; width: 1200px; height: 417px; overflow: hidden; background: var(--white); }
  .canvas { display: block; width: 1200px; height: 417px; }
  .card-title { font-family: "Rubik", sans-serif; font-weight: 500; font-size: 15.5px; fill: currentColor; }
  .card-title.compact { font-size: 12.4px; }
  .card-body { font-family: "Roboto", sans-serif; font-weight: 500; font-size: 8.4px; fill: currentColor; }
  .card-body.small { font-size: 6.6px; }
  .card-rule { stroke: currentColor; stroke-width: 1; }
  .icon { fill: none; stroke: currentColor; stroke-width: 1.6; stroke-linejoin: round; stroke-linecap: round; }
  .icon-fill { fill: currentColor; stroke: none; }
  .hub-title { font-family: "Rubik", sans-serif; font-weight: 700; font-size: 29px; fill: var(--ink); text-anchor: middle; }
  .ring { fill: var(--ring); }
  .hub { fill: var(--white); }
  .frame { fill: none; stroke: var(--frame); stroke-width: 1.5; }

  .solid .ink { color: var(--white); }
  .outline .ink { color: var(--ink); }
  .outline .shape { fill: var(--white); stroke: var(--ink); stroke-width: 3.5; }
  .color .ink { color: var(--ink); }
  .color .shape { fill: var(--white); stroke-width: 3.5; }
  .color .shape.doc { stroke: var(--line-doc); }
  .color .shape.sec { stroke: var(--line-sec); }
  .color .shape.erp { stroke: var(--line-erp); }
  .color .shape.dig { stroke: var(--line-dig); }
  .color .icon-doc { color: var(--icon-doc); }
  .color .icon-sec { color: var(--icon-sec); }
  .color .icon-erp { color: var(--icon-erp); }
  .color .icon-dig { color: var(--icon-dig); }
</style>
</head>
<body>
<svg class="canvas" viewBox="0 0 1920 667" xmlns="http://www.w3.org/2000/svg" role="img" aria-label="Super Product infographic shown in three colour variants">
  <defs>
    <linearGradient id="erp-gradient" x1="0" y1="0" x2="0" y2="1">
      <stop offset="0" stop-color="var(--blue-erp-a)"/>
      <stop offset="1" stop-color="var(--blue-erp-b)"/>
    </linearGradient>

    <path id="shape-doc" d="M90,178 A100,100 0 0 1 190,78 L288,78 A20,20 0 0 1 308,98 L308,306 A20,20 0 0 1 288,326 L110,326 A20,20 0 0 1 90,306 Z"/>
    <path id="shape-sec" d="M332,98 A20,20 0 0 1 352,78 L450,78 A100,100 0 0 1 550,178 L550,306 A20,20 0 0 1 530,326 L352,326 A20,20 0 0 1 332,306 Z"/>
    <path id="shape-erp" d="M90,365 A20,20 0 0 1 110,345 L288,345 A20,20 0 0 1 308,365 L308,573 A20,20 0 0 1 288,593 L190,593 A100,100 0 0 1 90,493 Z"/>
    <path id="shape-dig" d="M332,365 A20,20 0 0 1 352,345 L530,345 A20,20 0 0 1 550,365 L550,493 A100,100 0 0 1 450,593 L352,593 A20,20 0 0 1 332,573 Z"/>

    <g id="text-doc">
      <text class="card-title" x="241" y="116" text-anchor="end">Document</text>
      <text class="card-title" x="241" y="135" text-anchor="end">Management</text>
      <line class="card-rule" x1="120" y1="160" x2="288" y2="160"/>
      <text class="card-body" x="102" y="182">Streamline document organization, access, and</text>
      <text class="card-body" x="102" y="194">collaboration with easier file storage and sharing,</text>
      <text class="card-body" x="102" y="206">leading to more efficient workflows .</text>
      <text class="card-body" x="102" y="226">✓ Centralized Document Control</text>
      <text class="card-body" x="102" y="236">✓ Collaborative Workspace Integration</text>
      <text class="card-body" x="102" y="246">✓ Automated Compliance Tracking</text>
      <text class="card-body" x="102" y="257">✓ Check 4</text>
    </g>
    <g id="text-sec">
      <text class="card-title" x="395" y="113">Security</text>
      <text class="card-title" x="395" y="131">and Compliance</text>
      <line class="card-rule" x1="348" y1="160" x2="518" y2="160"/>
      <text class="card-body small" x="345" y="177">Benefit from tailored cloud solutions, secure data</text>
      <text class="card-body small" x="345" y="186">storage, and expert disaster recovery planning for</text>
      <text class="card-body small" x="345" y="195">reliable and scalable IT operations.</text>
      <text class="card-body small" x="409" y="227">✓ Custom Cloud Solutions</text>
      <text class="card-body small" x="409" y="236">✓ Secure Data Storage</text>
      <text class="card-body small" x="409" y="245">✓ Expert Disaster Recovery</text>
      <text class="card-body small" x="409" y="254">✓ Check 4</text>
    </g>
    <g id="text-erp">
      <text class="card-title compact" x="186" y="401" text-anchor="middle">Enterprise</text>
      <text class="card-title compact" x="107" y="416">Resource Planning</text>
      <line class="card-rule" x1="120" y1="439" x2="288" y2="439"/>
      <text class="card-body small" x="202" y="461" text-anchor="middle">Simplify management across finance, sales, and</text>
      <text class="card-body small" x="202" y="470" text-anchor="middle">operations, enabling better decision-making</text>
      <text class="card-body small" x="202" y="479" text-anchor="middle">and improved productivity.</text>
      <text class="card-body small" x="124" y="504">✓ Integrated Business Processes</text>
      <text class="card-body small" x="124" y="513">✓ Enhanced Decision-Making</text>
      <text class="card-body small" x="124" y="522">✓ Productivity Improvement</text>
      <text class="card-body small" x="124" y="531">✓ Check 4</text>
    </g>
    <g id="text-dig">
      <text class="card-title compact" x="432" y="401">Digital</text>
      <text class="card-title compact" x="432" y="417">Transformation</text>
      <line class="card-rule" x1="355" y1="439" x2="522" y2="439"/>
      <text class="card-body small" x="357" y="461">Turn scanned documents into easily searchable</text>
      <text class="card-body small" x="357" y="470">digital archives, boosting efficiency and</text>
      <text class="card-body small" x="357" y="479">accessibility.</text>
      <text class="card-body small" x="359" y="504">✓ Instant searchable Archives with OCR</text>
      <text class="card-body small" x="359" y="513">✓ Automated Document Classification</text>
      <text class="card-body small" x="359" y="522">✓ ShareHub and Cloud Blob Ready</text>
      <text class="card-body small" x="359" y="531">✓ Check 4</text>
    </g>

    <g id="icon-doc">
      <path class="icon" d="M256,104 H269 L275,110 V132 H256 Z"/>
      <path class="icon" d="M259,114 H272 M259,118 H272 M259,122 H272 M259,126 H272"/>
    </g>
    <g id="icon-sec">
      <path class="icon" style="stroke-width:2.2" d="M372,101 L385,106 V116 C385,125 379,130 372,133 C365,130 359,125 359,116 V106 Z"/>
      <path class="icon" style="stroke-width:2.2" d="M366,117 L370,121 L378,113"/>
    </g>
    <g id="icon-erp">
      <path class="icon" d="M115,373 H133 V397 H115 Z"/>
      <path class="icon" d="M111,369 H129 V393 H111 Z"/>
      <path class="icon" d="M114,375 H126 M114,379 H126 M114,383 H126 M114,387 H126"/>
    </g>
    <g id="icon-dig">
      <circle class="icon-fill" cx="514" cy="394" r="2.6"/>
      <path class="icon" style="stroke-width:3.4" d="M509.76,389.76 A6,6 0 0 1 518.24,389.76 M506.22,386.22 A11,11 0 0 1 521.78,386.22 M502.7,382.7 A16,16 0 0 1 525.3,382.7"/>
    </g>

    <g id="hub">
      <circle class="ring" cx="320" cy="340" r="108"/>
      <circle class="hub" cx="320" cy="340" r="85"/>
      <text class="hub-title" x="317" y="325">Super</text>
      <text class="hub-title" x="317" y="353">Product</text>
    </g>
  </defs>

  <g class="variant solid">
    <use href="#shape-doc" style="fill:var(--blue-doc)"/>
    <use href="#shape-sec" style="fill:var(--blue-sec)"/>
    <use href="#shape-erp" style="fill:url(#erp-gradient)"/>
    <use href="#shape-dig" style="fill:var(--blue-dig)"/>
    <g class="ink">
      <use href="#text-doc"/><use href="#text-sec"/><use href="#text-erp"/><use href="#text-dig"/>
      <use href="#icon-doc"/><use href="#icon-sec"/><use href="#icon-erp"/><use href="#icon-dig"/>
    </g>
    <use href="#hub"/>
  </g>

  <g class="variant outline" transform="translate(640,0)">
    <use class="shape" href="#shape-doc"/>
    <use class="shape" href="#shape-sec"/>
    <use class="shape" href="#shape-erp"/>
    <use class="shape" href="#shape-dig"/>
    <g class="ink">
      <use href="#text-doc"/><use href="#text-sec"/><use href="#text-erp"/><use href="#text-dig"/>
      <use href="#icon-doc"/><use href="#icon-sec"/><use href="#icon-erp"/><use href="#icon-dig"/>
    </g>
    <use href="#hub"/>
  </g>

  <g class="variant color" transform="translate(1280,0)">
    <use class="shape doc" href="#shape-doc"/>
    <use class="shape sec" href="#shape-sec"/>
    <use class="shape erp" href="#shape-erp"/>
    <use class="shape dig" href="#shape-dig"/>
    <g class="ink">
      <use href="#text-doc"/><use href="#text-sec"/><use href="#text-erp"/><use href="#text-dig"/>
    </g>
    <use class="icon-doc" href="#icon-doc"/>
    <use class="icon-sec" href="#icon-sec"/>
    <use class="icon-erp" href="#icon-erp"/>
    <use class="icon-dig" href="#icon-dig"/>
    <use href="#hub"/>
  </g>

  <rect class="frame" x="1" y="1" width="1918" height="665"/>
  <line class="frame" x1="640" y1="0" x2="640" y2="667"/>
  <line class="frame" x1="1280" y1="0" x2="1280" y2="667"/>
</svg>
</body>
</html>
```